Business Card Design

We are looking for a business card designed for our landscaping company. We do landscaping installation & Maintenance Services. We would like to see designs that have basic landscaping in background. We also think it is important to have both of our names and phone numbers on the card. We need something that stands out a little whether it is shape of the card or thickness or design.

Business

Bramblewood Yardworks, bramblewoodyard@mailvista.net, Owen Platt 555-273-9104, Daniel Korbin 555-618-3927

```html
<!DOCTYPE html>
<html lang="en">
<head>
<meta charset="utf-8">
<title>Bramblewood Yardworks — Business Card</title>
<link href="https://fonts.googleapis.com/css2?family=Tinos&display=swap" rel="stylesheet">
<style>
  :root {
    --backdrop: #e9e7e2;
    --card: #ffffff;
    --ink: #1a1a1a;
    --rule: #2a2a2a;
    --leaf: #5db344;
    --night: #050505;
  }
  html, body {
    margin: 0;
    width: 1200px;
    height: 902px;
    overflow: hidden;
    background: var(--backdrop);
  }
  .canvas {
    position: relative;
    width: 1200px;
    height: 902px;
  }
  .card {
    position: absolute;
    left: 100px;
    top: 165px;
    width: 1000px;
    height: 571px;
    background: var(--card);
    box-shadow: 0 10px 30px rgba(0,0,0,0.18);
    overflow: hidden;
    font-family: "Tinos", "Times New Roman", serif;
    color: var(--ink);
  }
  .card-bands {
    position: absolute;
    inset: 0;
  }
  .company-name {
    position: absolute;
    left: 0;
    right: 0;
    top: 100px;
    margin: 0;
    text-align: center;
    font-weight: 400;
    font-size: 70px;
    line-height: 1;
    letter-spacing: 0.5px;
  }
  .title-rule {
    position: absolute;
    left: 120px;
    width: 770px;
    top: 232px;
    height: 3px;
    background: var(--rule);
  }
  .contact-divider {
    position: absolute;
    left: 522px;
    top: 262px;
    width: 2px;
    height: 170px;
    background: var(--rule);
  }
  .contact {
    position: absolute;
    font-size: 40px;
    line-height: 1;
  }
  .contact .phone {
    display: flex;
    align-items: center;
    gap: 10px;
    margin-top: 12px;
    font-size: 28px;
  }
  .contact--left {
    right: 500px;
    top: 322px;
    text-align: right;
  }
  .contact--left .phone { justify-content: flex-end; }
  .contact--right {
    left: 548px;
    top: 282px;
  }
  .phone-icon {
    width: 22px;
    height: 22px;
    flex: none;
  }
  .email {
    position: absolute;
    right: 40px;
    bottom: 50px;
    color: #ffffff;
    font-size: 24px;
    line-height: 1;
    letter-spacing: 0.2px;
    white-space: nowrap;
  }
</style>
</head>
<body>
<div class="canvas">
  <div class="card">
    <svg class="card-bands" width="1000" height="571" viewBox="0 0 1000 571" aria-hidden="true">
      <path d="M0,492 L530,492 C555,492 568,478 576,458 L586,434 C594,416 610,408 632,408 L1000,408 L1000,571 L0,571 Z" fill="var(--leaf)"/>
      <path d="M580,571 L606,480 C613,455 630,440 660,440 L1000,440 L1000,571 Z" fill="var(--night)" stroke="#ffffff" stroke-width="4"/>
    </svg>

    <h1 class="company-name">Bramblewood Yardworks</h1>
    <div class="title-rule"></div>
    <div class="contact-divider"></div>

    <div class="contact contact--left">
      <div class="name">Owen Platt</div>
      <div class="phone">
        <span>555-273-9104</span>
        <svg class="phone-icon" viewBox="0 0 22 22" aria-hidden="true">
          <rect width="22" height="22" rx="2" fill="var(--night)"/>
          <path d="M7 5 L9 5 L10 8 L8.5 9.5 C9.5 11.5 10.5 12.5 12.5 13.5 L14 12 L17 13 L17 15 C17 16 16 17 15 17 C10 17 5 12 5 7 C5 6 6 5 7 5 Z" fill="#fff"/>
        </svg>
      </div>
    </div>

    <div class="contact contact--right">
      <div class="name">Daniel Korbin</div>
      <div class="phone">
        <svg class="phone-icon" viewBox="0 0 22 22" aria-hidden="true">
          <rect width="22" height="22" rx="2" fill="var(--night)"/>
          <path d="M7 5 L9 5 L10 8 L8.5 9.5 C9.5 11.5 10.5 12.5 12.5 13.5 L14 12 L17 13 L17 15 C17 16 16 17 15 17 C10 17 5 12 5 7 C5 6 6 5 7 5 Z" fill="#fff"/>
        </svg>
        <span>555-618-3927</span>
      </div>
    </div>

    <div class="email">bramblewoodyard@mailvista.net</div>
  </div>
</div>
</body>
</html>
```